Redesign Website - Current one too plain

The description is in the uploaded file. Please let me know if you need any more information. I'd prefer it if someone could implement the design to a WordPress site but the best design will win, regardless.
I would like the forms to look nice as well
UPDATE:
I don't think we can use the images that I provided, I think they make the site look a bit 'cheap' and I really don't know how to replace them. One thought I have had is to make the "Simple, Unique, Effective" a second feature on the right side of the page with the search on the left
Target Market(s)
Small companies, private sellers of cars and people who rent their caravan/holiday home out
Industry/Entity Type
Advertising
Number of Pages Required
3 page
Colors
Designer to choose colors to be used in the design.
Look and feel
Each slider illustrates characteristics of the customer's brand and the style your logo design should communicate.

```html
<!DOCTYPE html>
<html lang="en">
<head>
<meta charset="utf-8">
<title>Veltro – Create Your Advert</title>
<link href="https://fonts.googleapis.com/css2?family=Figtree:wght@400;500;600;700&display=swap" rel="stylesheet">
<style>
  :root {
    --lime: #e1fa1f;
    --brand: #a9d12e;
    --ink: #121212;
    --muted: #a8a4a6;
    --field: #f7f4f5;
    --hero: #dce4f5;
    --hero-deep: #e86a6a;
    --white: #ffffff;
  }
  * { box-sizing: border-box; margin: 0; padding: 0; }
  html, body { width: 990px; height: 1200px; overflow: hidden; background: var(--white); }
  body { font-family: "Figtree", sans-serif; color: var(--ink); position: relative; }

  .site-header { position: absolute; left: 133px; top: 26px; width: 724px; height: 33px; display: flex; align-items: center; }
  .brand { display: flex; align-items: center; gap: 6px; color: var(--brand); font-size: 19px; font-weight: 500; letter-spacing: 2px; }
  .brand-dot { width: 16px; height: 16px; border-radius: 50%; background: var(--brand); }
  .main-nav { position: absolute; left: 256px; display: flex; gap: 17px; font-size: 11px; font-weight: 500; }
  .main-nav a { color: var(--ink); text-decoration: none; }
  .main-nav a.is-active { color: var(--brand); }
  .login-btn { position: absolute; right: 0; width: 107px; height: 33px; border-radius: 17px; background: var(--lime); display: flex; align-items: center; justify-content: center; font-size: 12px; font-weight: 500; }

  .hero { position: absolute; left: 17px; top: 88px; width: 957px; height: 233px; border-radius: 16px; background: linear-gradient(90deg, var(--hero) 0%, var(--hero) 35%, var(--hero-deep) 36%, var(--hero-deep) 64%, #a7b3cf 65%, var(--hero) 100%); }

  .advert { position: absolute; left: 133px; top: 342px; width: 724px; }
  .advert-title { font-size: 26px; font-weight: 400; line-height: 1.2; }
  .advert-title strong { font-weight: 700; }
  .perks { display: flex; margin-top: 16px; height: 37px; }
  .perk { height: 37px; border-radius: 19px; background: var(--lime); display: flex; align-items: center; justify-content: center; font-size: 12px; font-weight: 500; }
  .perk:nth-child(1) { width: 139px; }
  .perk:nth-child(2) { width: 252px; margin-left: 13px; }
  .perk:nth-child(3) { width: 252px; margin-left: 18px; }
  .account-note { margin-top: 19px; font-size: 14px; }
  .account-note strong { font-weight: 600; }

  .field { display: block; width: 724px; height: 47px; border-radius: 10px; background: var(--field); padding: 0 29px; display: flex; align-items: center; font-size: 10.5px; color: var(--muted); }
  .field-name { margin-top: 14px; }
  .field-area { margin-top: 9px; }
  .field-web { margin-top: 10px; }
  .field-desc { margin-top: 11px; height: 111px; align-items: flex-start; padding-top: 16px; }

  .select-row { position: relative; height: 51px; display: flex; align-items: center; }
  .select-label { font-size: 14px; font-weight: 600; }
  .choice { position: absolute; display: flex; align-items: center; gap: 6px; font-size: 12px; }
  .choice::before { content: ""; width: 14px; height: 14px; border-radius: 50%; background: var(--field); }
  .choice.is-checked::before { background: radial-gradient(circle, var(--ink) 0 2.5px, var(--field) 3px); }
  .choice-car { left: 353px; }
  .choice-company { left: 486px; }
  .choice-holiday { left: 624px; }

  .char-count { margin-top: 15px; font-size: 10px; font-weight: 500; }
  .upload-title { margin-top: 24px; font-size: 14px; font-weight: 600; }
  .uploads { margin-top: 18px; display: flex; gap: 12px; }
  .upload-tile { width: 172px; height: 172px; border-radius: 9px; background: var(--field); display: flex; flex-direction: column; align-items: center; justify-content: center; gap: 6px; }
  .upload-tile.is-main { border: 1px solid #e6e2e4; }
  .upload-tile svg { width: 34px; height: 34px; }
  .upload-hint { font-size: 10px; font-weight: 500; text-align: center; line-height: 1.35; }

  .submit-btn { margin-top: 23px; margin-left: 1px; width: 129px; height: 35px; border-radius: 18px; background: var(--lime); display: flex; align-items: center; justify-content: space-between; padding: 0 16px 0 28px; font-size: 12px; font-weight: 600; }

  .site-footer { position: absolute; left: 133px; top: 1157px; width: 724px; display: flex; justify-content: space-between; font-size: 12px; }
  .site-footer strong { font-weight: 700; }
</style>
</head>
<body>
  <header class="site-header">
    <div class="brand"><span class="brand-dot"></span>VELTRO</div>
    <nav class="main-nav">
      <a class="is-active" href="#">Home</a>
      <a href="#">Advertise</a>
      <a href="#">Contact</a>
      <a href="#">Register</a>
    </nav>
    <div class="login-btn">LOGIN</div>
  </header>

  <div class="hero" role="img" aria-label="Illustration of a red car seen from above driving through snow, leaving tyre tracks"></div>

  <main class="advert">
    <h1 class="advert-title">Create Your <strong>Advert.</strong></h1>
    <div class="perks">
      <div class="perk">Free To Advertise</div>
      <div class="perk">Free graphics to print and display</div>
      <div class="perk">Weatherproof vinyl graphics available</div>
    </div>
    <p class="account-note"><strong>Login</strong> or <strong>Register</strong> to create your advert</p>

    <div class="field field-name">Enter Your Company Name, Make/Model Of Car, etc.</div>

    <div class="select-row">
      <span class="select-label">Select</span>
      <span class="choice choice-car">Car</span>
      <span class="choice choice-company is-checked">Company</span>
      <span class="choice choice-holiday">Holiday Name</span>
    </div>

    <div class="field field-area">Enter Town/City, County or Area.</div>
    <div class="field field-web">Enter Website or Social Media Pages.</div>
    <div class="field field-desc">Description - Include Price and Contact Details.</div>

    <p class="char-count">0 of 4000 max characters.</p>
    <h2 class="upload-title">Upload Images</h2>

    <div class="uploads">
      <div class="upload-tile is-main">
        <svg viewBox="0 0 34 34" fill="none" stroke="#121212" stroke-width="2" stroke-linecap="round" stroke-linejoin="round"><path d="M20 6H7a4 4 0 0 0-4 4v17a4 4 0 0 0 4 4h17a4 4 0 0 0 4-4V15"/><circle cx="11" cy="14" r="2.5"/><path d="M3 27c5-6 9-6 13-2s8 3 12-3"/><path d="M28 3v10M24 7l4-4 4 4"/></svg>
        <div class="upload-hint">*Upload<br>Main Images First</div>
      </div>
      <div class="upload-tile">
        <svg viewBox="0 0 34 34" fill="none" stroke="#121212" stroke-width="2" stroke-linecap="round" stroke-linejoin="round"><path d="M20 6H7a4 4 0 0 0-4 4v17a4 4 0 0 0 4 4h17a4 4 0 0 0 4-4V15"/><circle cx="11" cy="14" r="2.5"/><path d="M3 27c5-6 9-6 13-2s8 3 12-3"/><path d="M28 3v10M24 7l4-4 4 4"/></svg>
      </div>
      <div class="upload-tile">
        <svg viewBox="0 0 34 34" fill="none" stroke="#121212" stroke-width="2" stroke-linecap="round" stroke-linejoin="round"><path d="M20 6H7a4 4 0 0 0-4 4v17a4 4 0 0 0 4 4h17a4 4 0 0 0 4-4V15"/><circle cx="11" cy="14" r="2.5"/><path d="M3 27c5-6 9-6 13-2s8 3 12-3"/><path d="M28 3v10M24 7l4-4 4 4"/></svg>
      </div>
      <div class="upload-tile">
        <svg viewBox="0 0 34 34" fill="none" stroke="#121212" stroke-width="2" stroke-linecap="round" stroke-linejoin="round"><path d="M20 6H7a4 4 0 0 0-4 4v17a4 4 0 0 0 4 4h17a4 4 0 0 0 4-4V15"/><circle cx="11" cy="14" r="2.5"/><path d="M3 27c5-6 9-6 13-2s8 3 12-3"/><path d="M28 3v10M24 7l4-4 4 4"/></svg>
      </div>
    </div>

    <div class="submit-btn">Submit
      <svg width="16" height="12" viewBox="0 0 16 12" fill="none" stroke="#121212" stroke-width="1.6" stroke-linecap="round" stroke-linejoin="round"><path d="M1 6h14M10 1l5 5-5 5"/></svg>
    </div>
  </main>

  <footer class="site-footer">
    <span>© 2023 <strong>VELTRO.</strong> All rights reserved.</span>
    <span>Terms &amp; Conditions &nbsp;|&nbsp; Privacy Policy</span>
  </footer>
</body>
</html>
```